Business Card Design Project

Doctor, Pain Management. Need a new business card design with appointment info on the back. New address is 18 Corvell Road, Suite 304, Brisdale, NJ 07391. Right now I believe the rest of the information is staying the same.

```html
<!DOCTYPE html>
<html lang="en">
<head>
<meta charset="utf-8">
<title>Gentle Relief Pain Care – Business Card</title>
<link href="https://fonts.googleapis.com/css2?family=Tinos&family=Open+Sans:ital,wght@0,400;0,600;0,700;1,400&display=swap" rel="stylesheet">
<style>
  :root {
    --stage: #e9e6e1;
    --card-white: #ffffff;
    --card-black: #1c1d1f;
    --sky: #7fd3f2;
    --gold: #e3d62a;
    --ink-grey: #9a9694;
    --ink-dark: #1a1a1a;
    --rule: #6b6b6b;
  }
  * { margin: 0; padding: 0; box-sizing: border-box; }
  html, body { width: 1200px; height: 950px; overflow: hidden; }
  body { background: var(--stage); position: relative; }

  .card {
    position: absolute;
    background: var(--card-white);
    box-shadow: 0 10px 28px rgba(0,0,0,0.22);
    overflow: hidden;
  }

  /* Front */
  .card-front { left: 70px; top: 140px; width: 380px; height: 665px; }
  .front-art { position: absolute; inset: 0; }
  .brand {
    position: absolute; left: 46px; top: 120px;
    display: flex; align-items: center; gap: 14px;
  }
  .brand-dot { width: 34px; height: 34px; border-radius: 50%; background: var(--sky); }
  .brand-name {
    font-family: "Tinos", serif; font-size: 27px; color: var(--gold); letter-spacing: 0.5px;
  }
  .identity {
    position: absolute; right: 34px; top: 440px; text-align: right;
    font-family: "Tinos", serif;
  }
  .doctor-name { font-size: 25px; color: var(--sky); line-height: 1.1; }
  .doctor-title { font-size: 17px; color: var(--ink-grey); margin-top: 2px; }
  .contact { margin-top: 14px; font-size: 15px; color: var(--ink-grey); line-height: 1.35; }
  .contact-line { display: flex; justify-content: flex-end; align-items: center; gap: 8px; }
  .contact-line svg { width: 13px; height: 13px; fill: var(--ink-grey); }

  /* Back */
  .card-back {
    left: 500px; top: 285px; width: 640px; height: 366px;
    font-family: "Open Sans", sans-serif; color: var(--ink-dark);
  }
  .back-title {
    position: absolute; top: 30px; left: 0; right: 0; text-align: center;
    font-size: 27px; font-weight: 600;
  }
  .field {
    position: absolute; left: 44px; right: 44px;
    display: flex; align-items: flex-end; gap: 8px; font-size: 19px;
  }
  .field .dots { flex: 1; border-bottom: 2px dotted var(--rule); height: 1px; margin-bottom: 6px; }
  .field-name { top: 100px; }
  .field-date { top: 150px; }
  .field-time { top: 250px; }
  .field-time .suffix { font-size: 13px; margin-bottom: 2px; }
  .days {
    position: absolute; left: 44px; right: 44px; top: 200px;
    display: flex; justify-content: space-between; font-size: 18px;
  }
  .day { display: flex; align-items: center; gap: 5px; }
  .box { width: 15px; height: 15px; border: 1.5px solid var(--ink-dark); }
  .notice {
    position: absolute; left: 44px; right: 44px; top: 302px;
    font-size: 13.5px; font-style: italic; text-align: center; line-height: 1.35;
  }
</style>
</head>
<body>

<section class="card card-front">
  <svg class="front-art" viewBox="0 0 380 665" preserveAspectRatio="none" aria-hidden="true">
    <path d="M0 0 H380 V345 C300 395 170 320 0 345 Z" fill="var(--card-black)"/>
    <path d="M0 345 C170 320 300 395 380 345 V360 C300 410 170 335 0 362 Z" fill="var(--sky)"/>
    <path d="M0 362 C170 335 300 410 380 360 V364 C300 414 170 340 0 366 Z" fill="var(--card-black)"/>
  </svg>
  <div class="brand">
    <span class="brand-dot"></span>
    <span class="brand-name">Gentle Relief Pain Care</span>
  </div>
  <div class="identity">
    <p class="doctor-name">Lian Zhou, M.D., Ph.D.</p>
    <p class="doctor-title">Board Certified Anesthiologist</p>
    <div class="contact">
      <p class="contact-line">18 Corvell Road</p>
      <p class="contact-line">Suite 304</p>
      <p class="contact-line">Brisdale, NJ 07391</p>
      <p class="contact-line">973.555.0148
        <svg viewBox="0 0 16 16"><path d="M3 1l3 3-2 2c1 2 3 4 5 5l2-2 3 3-2 3C6 14 2 10 1 3z"/></svg></p>
      <p class="contact-line">973.555.0162
        <svg viewBox="0 0 16 16"><rect x="3" y="1" width="10" height="4"/><rect x="1" y="6" width="14" height="6" rx="1"/><rect x="4" y="11" width="8" height="4"/></svg></p>
      <p class="contact-line">reliefclinic.office@mail.com
        <svg viewBox="0 0 16 16"><path d="M1 3h14v10H1z M1 3l7 6 7-6" fill="none" stroke="var(--ink-grey)" stroke-width="1.6"/></svg></p>
      <p class="contact-line">www.gentlereliefpc.com
        <svg viewBox="0 0 16 16"><circle cx="8" cy="8" r="7"/></svg></p>
    </div>
  </div>
</section>

<section class="card card-back">
  <h2 class="back-title">Next Appointment</h2>
  <div class="field field-name"><span>Name :</span><span class="dots"></span></div>
  <div class="field field-date"><span>Date :</span><span class="dots"></span></div>
  <div class="days">
    <span class="day">Mon <span class="box"></span></span>
    <span class="day">Tue <span class="box"></span></span>
    <span class="day">Wed <span class="box"></span></span>
    <span class="day">Thu <span class="box"></span></span>
    <span class="day">Fri <span class="box"></span></span>
    <span class="day">Sat <span class="box"></span></span>
  </div>
  <div class="field field-time"><span>Time :</span><span class="dots"></span><span class="suffix">AM/PM</span></div>
  <p class="notice">Please give 24 hours notice if you are unable to keep your appointment or<br>a cancellation fee may be charged.</p>
</section>

</body>
</html>
```